UX - Need some screens design for a Skill Assessment Application

I am building an app to carry out skill assessments. Depending on how the assessment is configured, it may have one or more parts
1. Question based assessment (Multiple Choice, True False, Fill in the blanks"
2. Endorsement by two colleagues - A screen that allows user to pick colleagues based on search and shows the status of pending requests
3. A written submission - a page that explains the format of the submission and a file upload
As each assessment can be configured with or without any of the steps, the assessment UI must be such that these areas get hidden/displayed based on configuration.
Colour codes to be used can be #0e78bb and #ffffff
There will also be a start screen (instructions) and an end screen (results)
Target Market(s)
Enterprise software
Number of Pages Required
4 page

```html
<!DOCTYPE html>
<html lang="en">
<head>
<meta charset="utf-8">
<title>Skillwise – Assessments</title>
<link href="https://fonts.googleapis.com/css2?family=Inter:wght@400;500;600;700&display=swap" rel="stylesheet">
<style>
:root{
  --hero:#0355b0;
  --tile:#1a68be;
  --tile-icon:#2c79cb;
  --accent:#0e78bb;
  --button:#1479c4;
  --white:#ffffff;
  --page:#f4f5f7;
  --ink:#1f2328;
  --muted:#555b63;
  --link:#0e6fb5;
  --chip:#ececec;
  --check:#0e9a9a;
  --nav-soft:#c9dcf2;
  --divider:rgba(255,255,255,.18);
}
*{box-sizing:border-box;margin:0;padding:0}
html,body{width:1200px;height:771px;overflow:hidden}
body{font-family:"Inter",sans-serif;background:var(--page);color:var(--ink);position:relative}
.hero{position:absolute;left:0;top:0;width:1200px;height:288px;background:var(--hero);color:var(--white)}
.topbar{position:absolute;left:0;top:0;width:1200px;height:43px;border-bottom:1px solid var(--divider)}
.brand{position:absolute;left:70px;top:12px;display:flex;align-items:center;gap:8px;font-size:15px;font-weight:600}
.brand-dot{width:18px;height:18px;border-radius:50%;background:var(--white)}
.nav{position:absolute;left:488px;top:0;display:flex;gap:20px;height:43px}
.nav a{color:var(--nav-soft);text-decoration:none;font-size:12.5px;line-height:45px;position:relative}
.nav a.active{color:var(--white);font-weight:600}
.nav a.active::after{content:"";position:absolute;left:0;right:0;bottom:-1px;height:3px;background:#3ea6ea}
.top-actions{position:absolute;right:70px;top:8px;display:flex;align-items:center;gap:16px}
.avatar{border-radius:50%;background:linear-gradient(135deg,#3b4d63,#c9a18b)}
.avatar.small{width:27px;height:27px;border:2px solid var(--white)}
.welcome{position:absolute;left:57px;top:71px;display:flex;align-items:center;gap:21px}
.avatar.large{width:43px;height:43px}
.welcome-hi{font-size:12px;color:var(--nav-soft)}
.welcome-name{font-size:17px;font-weight:600;margin-top:4px}
.create-btn{position:absolute;left:965px;top:75px;width:177px;height:34px;border-radius:3px;background:var(--button);color:var(--white);font-size:11.5px;font-weight:500;display:flex;align-items:center;justify-content:center;gap:8px}
.summary-label{position:absolute;left:57px;top:141px;font-size:14px;font-weight:500}
.summary{position:absolute;left:57px;top:171px;display:flex;gap:15px}
.stat{width:260px;height:89px;background:var(--tile);border-radius:3px;position:relative}
.stat-icon{position:absolute;left:14px;top:14px;width:34px;height:34px;border-radius:2px;background:var(--tile-icon);display:flex;align-items:center;justify-content:center}
.stat-num{position:absolute;left:65px;top:20px;font-size:17px;font-weight:600}
.stat-label{position:absolute;left:65px;top:47px;font-size:12px;font-weight:500}
.stat-sub{position:absolute;left:65px;top:64px;font-size:9.5px;color:var(--nav-soft)}
.section-title{position:absolute;left:71px;top:309px;font-size:17px;font-weight:600}
.tabs{position:absolute;left:71px;top:349px;display:flex;height:31px;border-radius:3px;overflow:hidden}
.tab{padding:0 17px;font-size:11.5px;line-height:31px;background:#e4e6e9;color:var(--muted)}
.tab b{font-weight:600}
.tab.active{background:var(--accent);color:var(--white)}
.views{position:absolute;left:1075px;top:355px;display:flex;gap:15px}
.card{position:absolute;width:339px;height:167px;background:var(--white);border-radius:3px;box-shadow:0 1px 3px rgba(0,0,0,.05)}
.card-id{position:absolute;left:21px;top:21px;font-size:12px;color:var(--muted)}
.card-menu{position:absolute;right:21px;top:21px}
.card-title{position:absolute;left:21px;top:44px;font-size:12px;color:var(--link);font-weight:500}
.meta{position:absolute;top:73px;font-size:9px;color:var(--muted);letter-spacing:.2px}
.meta span{display:block;font-size:12px;letter-spacing:0;margin-top:5px;color:var(--muted)}
.chips{position:absolute;left:21px;top:124px;display:flex;gap:8px}
.chip{height:22px;border-radius:11px;background:var(--chip);padding:0 6px 0 9px;display:flex;align-items:center;gap:7px;font-size:11.5px;color:var(--muted)}
</style>
</head>
<body>
<header class="hero">
  <div class="topbar">
    <div class="brand"><span class="brand-dot"></span>Skillwise</div>
    <nav class="nav"><a class="active" href="#">Assessments</a><a href="#">Colleagues</a><a href="#">Results</a></nav>
    <div class="top-actions">
      <svg width="18" height="18" viewBox="0 0 24 24" fill="none" stroke="#fff" stroke-width="1.6"><path d="M6 17V11a6 6 0 0 1 12 0v6l1.5 2h-15z"/><path d="M10 21h4"/></svg>
      <svg width="18" height="18" viewBox="0 0 24 24" fill="none" stroke="#fff" stroke-width="1.6"><circle cx="12" cy="12" r="3"/><path d="M12 2.5l2 2.3 3-.6.8 2.9 2.8 1.2-1 2.8 1 2.8-2.8 1.2-.8 2.9-3-.6-2 2.3-2-2.3-3 .6-.8-2.9-2.8-1.2 1-2.8-1-2.8 2.8-1.2.8-2.9 3 .6z"/></svg>
      <div class="avatar small" role="img" aria-label="User profile photo"></div>
    </div>
  </div>
  <div class="welcome">
    <div class="avatar large" role="img" aria-label="User profile photo"></div>
    <div><div class="welcome-hi">Welcome back!</div><div class="welcome-name">Maya L. Hartono</div></div>
  </div>
  <div class="create-btn">
    <svg width="13" height="13" viewBox="0 0 24 24" fill="none" stroke="#fff" stroke-width="2"><path d="M14 21H5V3h12v8"/><path d="M8 8h6M8 12h3"/><circle cx="17" cy="17" r="3"/><path d="M19.5 19.5L22 22"/></svg>
    Create New Assessment
  </div>
  <div class="summary-label">Summary</div>
  <div class="summary">
    <div class="stat"><div class="stat-icon"><svg width="22" height="22" viewBox="0 0 24 24" fill="none" stroke="#fff" stroke-width="1.5"><path d="M14 21H4V3h13v8"/><path d="M7 8h7M7 12h4M7 16h3"/><circle cx="17" cy="17" r="3.5"/><path d="M15.5 17l1 1 2-2"/></svg></div><div class="stat-num">7</div><div class="stat-label">My Assessments</div><div class="stat-sub">3 pending</div></div>
    <div class="stat"><div class="stat-icon"><svg width="22" height="22" viewBox="0 0 24 24" fill="none" stroke="#fff" stroke-width="1.5"><path d="M12 2l1.5 3 3 .4-2.2 2 .6 3L12 9l-2.9 1.4.6-3-2.2-2 3-.4z"/><path d="M3 13h3v8H3zM6 14h5l2 2h5a2 2 0 0 1 0 4H6"/></svg></div><div class="stat-num">3</div><div class="stat-label">Endorsements</div><div class="stat-sub">1 pending</div></div>
    <div class="stat"><div class="stat-icon"><svg width="22" height="22" viewBox="0 0 24 24" fill="none" stroke="#fff" stroke-width="1.5"><circle cx="6" cy="6" r="2.5"/><circle cx="18" cy="6" r="2.5"/><circle cx="12" cy="12" r="2.5"/><path d="M2 13a4 4 0 0 1 6-2M22 13a4 4 0 0 0-6-2M7 21a5 5 0 0 1 10 0"/></svg></div><div class="stat-num">10</div><div class="stat-label">Colleagues</div><div class="stat-sub">Last updated on May 23, 2024</div></div>
    <div class="stat"><div class="stat-icon"><svg width="22" height="22" viewBox="0 0 24 24" fill="none" stroke="#fff" stroke-width="1.5"><path d="M12 14V3M8 7l4-4 4 4"/><path d="M7 11H3v10h18V11h-4"/><path d="M3 16h5l1 2h6l1-2h5"/></svg></div><div class="stat-num">7</div><div class="stat-label">Submissions</div><div class="stat-sub">Last submit on May 23, 2024</div></div>
  </div>
</header>

<main>
  <h2 class="section-title">Assessments</h2>
  <div class="tabs"><div class="tab">Pending <b>2</b></div><div class="tab active">Completed <b>5</b></div></div>
  <div class="views">
    <svg width="20" height="18" viewBox="0 0 20 18" fill="none" stroke="#0e78bb" stroke-width="1.6"><path d="M6 3h13M6 9h13M6 15h13M1 3h2M1 9h2M1 15h2"/></svg>
    <svg width="19" height="19" viewBox="0 0 19 19" fill="none" stroke="#7a8089" stroke-width="1.4"><rect x="1" y="1" width="7" height="7"/><rect x="11" y="1" width="7" height="7"/><rect x="1" y="11" width="7" height="7"/><rect x="11" y="11" width="7" height="7"/></svg>
  </div>

  <svg width="0" height="0" style="position:absolute"><defs>
    <symbol id="tick" viewBox="0 0 14 14"><circle cx="7" cy="7" r="7" fill="#0e9a9a"/><path d="M4 7.2l2 2 4-4" fill="none" stroke="#fff" stroke-width="1.6"/></symbol>
    <symbol id="dots" viewBox="0 0 4 16"><circle cx="2" cy="2" r="1.6" fill="#555"/><circle cx="2" cy="8" r="1.6" fill="#555"/><circle cx="2" cy="14" r="1.6" fill="#555"/></symbol>
  </defs></svg>

  <article class="card" style="left:71px;top:400px">
    <div class="card-id">1723091983</div><svg class="card-menu" width="4" height="16"><use href="#dots"/></svg>
    <div class="card-title">UI/UX Designer Assessments</div>
    <div class="meta" style="left:21px">PUBLISHED ON<span>20/05/2024</span></div>
    <div class="meta" style="left:146px">DUE DATE<span>24/05/2024</span></div>
    <div class="chips"><div class="chip">Quiz<svg width="14" height="14"><use href="#tick"/></svg></div><div class="chip">Endorsement<svg width="14" height="14"><use href="#tick"/></svg></div></div>
  </article>
  <article class="card" style="left:430px;top:400px">
    <div class="card-id">1723091983</div><svg class="card-menu" width="4" height="16"><use href="#dots"/></svg>
    <div class="card-title">Front-end Developer Assessments</div>
    <div class="meta" style="left:21px">PUBLISHED ON<span>20/05/2024</span></div>
    <div class="meta" style="left:146px">DUE DATE<span>24/05/2024</span></div>
    <div class="chips"><div class="chip">Endorsement<svg width="14" height="14"><use href="#tick"/></svg></div><div class="chip">Submission<svg width="14" height="14"><use href="#tick"/></svg></div></div>
  </article>
  <article class="card" style="left:789px;top:400px">
    <div class="card-id">1723091983</div><svg class="card-menu" width="4" height="16"><use href="#dots"/></svg>
    <div class="card-title">Cybersecurity Analyst Assessments</div>
    <div class="meta" style="left:21px">PUBLISHED ON<span>20/05/2024</span></div>
    <div class="meta" style="left:146px">DUE DATE<span>24/05/2024</span></div>
    <div class="chips"><div class="chip">Quiz<svg width="14" height="14"><use href="#tick"/></svg></div></div>
  </article>
  <article class="card" style="left:71px;top:587px">
    <div class="card-id">1723091983</div><svg class="card-menu" width="4" height="16"><use href="#dots"/></svg>
    <div class="card-title">DevOps Engineer Assessments</div>
    <div class="meta" style="left:21px">PUBLISHED ON<span>20/05/2024</span></div>
    <div class="meta" style="left:146px">DUE DATE<span>24/05/2024</span></div>
    <div class="chips"><div class="chip">Quiz<svg width="14" height="14"><use href="#tick"/></svg></div><div class="chip">Endorsement<svg width="14" height="14"><use href="#tick"/></svg></div><div class="chip">Submission<svg width="14" height="14"><use href="#tick"/></svg></div></div>
  </article>
  <article class="card" style="left:430px;top:587px">
    <div class="card-id">1723091983</div><svg class="card-menu" width="4" height="16"><use href="#dots"/></svg>
    <div class="card-title">Sales Representative Assessments</div>
    <div class="meta" style="left:21px">PUBLISHED ON<span>20/05/2024</span></div>
    <div class="meta" style="left:146px">DUE DATE<span>24/05/2024</span></div>
    <div class="chips"><div class="chip">Quiz<svg width="14" height="14"><use href="#tick"/></svg></div><div class="chip">Endorsement<svg width="14" height="14"><use href="#tick"/></svg></div></div>
  </article>
</main>
</body>
</html>
```